Property Services Company Needs a Brochure Design

Looking for a new brochure design for an existing property services company.

We provide a range of property services from, market research, real estate brokerage, valuation and appraisal, property development and other real estate consulting services.

We would like a fresh modern brochure design with good graphics and features. Our colours are white, blue and orange.

The design should communicate, attention to detail, superior service delivery and distinction in results.
Updates

I would like the brochure to be roughly about 20 pages.

Containing the following,

1) An introduction
2) Contents Page
2) What we do
3) Our Services
4) Agency & Brokerage
5) Real Estate Consulting
6) Market Research
7) Appraisal & Valuation
8) Project Management
9) Property Development

I would also like icons to represent items 4,5,6,7,8 & 9, they should be represented vertically on each of the pages from the contents page and highlighted individually on the pages that they represent.. i.e. on appraisal & valuation page, all six icons will be arranged vertically and the appraisal and valuations icon will be highlighted.

I will also like to have images that depict the services on the various pages.

I have some pages I think will flow which I will upload shortly.

Industry/Entity Type

Real Estate

Font styles to use
Serif

Colors
f78f20
0455a3

```html
<!DOCTYPE html>
<html lang="en">
<head>
<meta charset="utf-8">
<title>Halvern Property Services – Brochure Spread</title>
<link rel="stylesheet" href="https://fonts.googleapis.com/css2?family=Crimson+Text:wght@400;600;700&family=Open+Sans:wght@400;600&display=swap">
<style>
  :root {
    --backdrop: #cfcfcf;
    --paper: #ffffff;
    --paper-shade: #f4f4f5;
    --brand-purple: #544d78;
    --brand-orange: #ee7b30;
    --ink: #3a3a44;
    --ink-soft: #5c5c66;
  }
  * { box-sizing: border-box; margin: 0; padding: 0; }
  html, body {
    width: 1200px; height: 800px; overflow: hidden;
    background: var(--backdrop);
  }
  .spread {
    position: absolute; left: 180px; top: 100px;
    width: 840px; height: 600px;
    display: flex;
    box-shadow: 0 12px 30px rgba(0,0,0,0.18);
  }
  .page { position: relative; width: 420px; height: 600px; overflow: hidden; background: var(--paper); }

  /* Inside page */
  .intro { position: absolute; left: 40px; top: 38px; width: 340px; }
  .intro-heading {
    font-family: "Crimson Text", serif; font-weight: 700;
    font-size: 13px; letter-spacing: 0.06em; color: var(--brand-orange);
    margin-bottom: 4px;
  }
  .intro-text {
    font-family: "Crimson Text", serif; font-size: 9.6px; line-height: 1.35;
    color: var(--ink); margin-bottom: 5px; text-align: justify;
  }
  .feature-photo-wrap { position: absolute; left: 88px; top: 300px; width: 244px; height: 132px; }
  .frame-purple { position: absolute; left: -8px; top: -8px; width: 244px; height: 132px; border: 3px solid var(--brand-purple); }
  .frame-orange { position: absolute; left: 8px; top: 8px; width: 244px; height: 132px; border: 3px solid var(--brand-orange); }
  .feature-photo {
    position: absolute; inset: 0;
    background: linear-gradient(135deg, #eceef0 0%, #c9ccd0 45%, #8f9399 100%);
  }

  .brand-block { position: absolute; left: 0; width: 100%; top: 470px; text-align: center; }
  .brand-name {
    display: inline-flex; align-items: center; gap: 7px;
    font-family: "Crimson Text", serif; font-weight: 600;
    font-size: 19px; color: var(--brand-purple); line-height: 1;
  }
  .brand-square { width: 12px; height: 12px; background: var(--brand-orange); }
  .contact {
    font-family: "Open Sans", sans-serif; font-size: 8.4px; color: var(--ink-soft);
    margin-top: 7px; line-height: 1.55;
  }
  .contact-line { display: flex; justify-content: center; align-items: center; gap: 10px; }
  .contact-item { display: inline-flex; align-items: center; gap: 3px; }
  .contact-icon { width: 9px; height: 9px; }
  .band-purple-thin { position: absolute; left: 0; right: 0; top: 560px; height: 4px; background: var(--brand-purple); }
  .band-orange { position: absolute; left: 0; right: 0; top: 570px; height: 10px; background: var(--brand-orange); }

  /* Cover page */
  .cover .top-band { position: absolute; left: 0; right: 0; top: 0; height: 46px; background: var(--brand-purple); }
  .cover .top-rule { position: absolute; left: 0; right: 0; top: 54px; height: 6px; background: var(--brand-orange); }
  .cover-photo {
    position: absolute; left: 0; right: 0; top: 60px; height: 350px;
    background: linear-gradient(160deg, #e9e6df 0%, #c8bfae 40%, #9c907c 75%, #b8ad98 100%);
  }
  .cover-brand { position: absolute; right: 28px; top: 78px; }
  .cover-brand .brand-name { font-size: 22px; }
  .cover .white-strip { position: absolute; left: 0; right: 0; top: 410px; height: 12px; background: var(--paper); }
  .cover .bottom-block { position: absolute; left: 0; right: 0; top: 422px; bottom: 0; background: var(--brand-purple); }
  .fold { position: absolute; left: 0; top: 0; bottom: 0; width: 10px; background: linear-gradient(90deg, rgba(0,0,0,0.12), rgba(0,0,0,0)); }
</style>
</head>
<body>
  <main class="spread">
    <section class="page inside-page">
      <div class="intro">
        <h2 class="intro-heading">INTRODUCTION</h2>
        <p class="intro-text">HALVERN was incorporated in 1983 as an interior design and property development company. Over the years we have expanded our service with a foundation based on core strengths, unrivalled local expertise, network and knowledge combined with strategic partnerships.</p>
        <p class="intro-text">Halvern offers a comprehensive range of services on a local, regional, national and international basis to owners, investors and occupiers within the residential and commercial property market.</p>
        <p class="intro-text">Our clients depend on our ability to draw on professional teams with years of experience in the local market, our knowledge of the property market inside and out, and provide workable, creative solutions to all their real estate needs.</p>
        <p class="intro-text">We currently provide services to corporations, financial institutions, government agencies, public sector bodies, developers and investors. Our knowledge, expertise, experience and technological resources allow us to be a superior service provider.</p>
      </div>

      <div class="feature-photo-wrap">
        <div class="frame-purple"></div>
        <div class="frame-orange"></div>
        <div class="feature-photo" role="img" aria-label="Photo of a bright modern office with a glass desk and an ergonomic chair"></div>
      </div>

      <div class="brand-block">
        <div class="brand-name"><span class="brand-square"></span>Halvern Property Services</div>
        <div class="contact">
          <div class="contact-line">
            <span class="contact-item">
              <svg class="contact-icon" viewBox="0 0 10 10" aria-hidden="true"><path d="M5 0.5a3.3 3.3 0 0 0-3.3 3.3C1.7 6.3 5 9.5 5 9.5s3.3-3.2 3.3-5.7A3.3 3.3 0 0 0 5 0.5z" fill="#ee7b30"/><circle cx="5" cy="3.8" r="1.2" fill="#fff"/></svg>
              12th Floor, Harbour House, 58 Marina Road
            </span>
          </div>
          <div class="contact-line">Lagos, Nigeria</div>
          <div class="contact-line">
            <span class="contact-item">
              <svg class="contact-icon" viewBox="0 0 10 10" aria-hidden="true"><path d="M2.2 0.8l1.6 1.9-0.9 1.2c0.6 1.3 1.5 2.2 2.8 2.8l1.2-0.9 1.9 1.6-0.9 1.6C4.3 8.9 1.1 5.7 0.8 1.7z" fill="#ee7b30"/></svg>
              +234 1 555 0142
            </span>
            <span class="contact-item">
              <svg class="contact-icon" viewBox="0 0 10 10" aria-hidden="true"><path d="M2.2 0.8l1.6 1.9-0.9 1.2c0.6 1.3 1.5 2.2 2.8 2.8l1.2-0.9 1.9 1.6-0.9 1.6C4.3 8.9 1.1 5.7 0.8 1.7z" fill="#ee7b30"/></svg>
              +234 1 555 0187
            </span>
          </div>
          <div class="contact-line">
            <span class="contact-item">
              <svg class="contact-icon" viewBox="0 0 10 10" aria-hidden="true"><rect x="0.5" y="2" width="9" height="6" fill="#544d78"/><path d="M0.5 2l4.5 3.5L9.5 2" stroke="#fff" stroke-width="0.8" fill="none"/></svg>
              info@halvernproperty.com
            </span>
            <span class="contact-item">
              <svg class="contact-icon" viewBox="0 0 10 10" aria-hidden="true"><circle cx="5" cy="5" r="4.3" fill="none" stroke="#544d78" stroke-width="0.9"/><path d="M0.7 5h8.6M5 0.7c-2.2 2.6-2.2 6 0 8.6M5 0.7c2.2 2.6 2.2 6 0 8.6" stroke="#544d78" stroke-width="0.7" fill="none"/></svg>
              www.halvernproperty.com
            </span>
          </div>
        </div>
      </div>

      <div class="band-purple-thin"></div>
      <div class="band-orange"></div>
    </section>

    <section class="page cover">
      <div class="top-band"></div>
      <div class="top-rule"></div>
      <div class="cover-photo" role="img" aria-label="Photo of a spacious modern office lobby with glass walls and polished floors"></div>
      <div class="cover-brand">
        <div class="brand-name"><span class="brand-square"></span>Halvern Property Services</div>
      </div>
      <div class="white-strip"></div>
      <div class="bottom-block"></div>
      <div class="fold"></div>
    </section>
  </main>
</body>
</html>
```